Letterhead and matching envelope design for a dental office

We need a new stationary design, letterhead and envelope #10, for a dental office in Denver area. We are called Bright Harbor Dental. We want a simple and minimalistic design but not a boring design. I wish to have one good point that makes it look professional. I have attached our logo. Feel free to use either one. I want the design for letterhead and envelope look like a "matching pair" but not look the same. The envelope doesn't have to be white and it will have an address window on bottom left.

Target Market(s)

everyone who visits dentist (adults)

Industry/Entity Type

Dental

Font styles to use
Other font styles liked:
• close to font on logo or something that matches well

Requirements
Must have
• professional
• simple, minimalistic
• unique point that stands out
Nice to have
• matching but not same design for letterhead and envelope
Should not have
• not look like all the other boring designs
• no flowery, distracting feats

```html
<!DOCTYPE html>
<html lang="en">
<head>
<meta charset="utf-8">
<title>Bright Harbor Dental – Letterhead</title>
<link href="https://fonts.googleapis.com/css2?family=Arimo:wght@400;700&display=swap" rel="stylesheet">
<style>
  :root {
    --backdrop: #e9e9e7;
    --paper: #ffffff;
    --brand-green: #3bb54a;
    --leaf-tint: #d7ebd2;
    --leaf-soft: #eef6ec;
    --ink: #333333;
    --ink-soft: #555555;
  }
  * { margin: 0; padding: 0; box-sizing: border-box; }
  html, body {
    width: 1200px; height: 795px; overflow: hidden;
    background: var(--backdrop);
    font-family: "Arimo", Arial, sans-serif;
  }
  .letterhead {
    position: absolute; left: 338px; top: 20px;
    width: 524px; height: 755px;
    background: var(--paper);
    box-shadow: 0 4px 18px rgba(0,0,0,.12);
    overflow: hidden;
  }
  .brand {
    position: absolute; left: 44px; top: 48px;
    display: flex; align-items: center; gap: 8px;
  }
  .brand__dot { width: 12px; height: 12px; border-radius: 50%; background: var(--brand-green); }
  .brand__name { color: var(--brand-green); font-size: 17px; font-weight: 700; letter-spacing: .08em; text-transform: uppercase; }
  .contact {
    position: absolute; right: 40px; top: 44px;
    list-style: none; text-align: right;
    font-size: 9px; line-height: 14px; color: var(--ink);
  }
  .contact li { display: flex; justify-content: flex-end; align-items: center; gap: 5px; }
  .contact__icon { width: 10px; height: 10px; border-radius: 50%; background: var(--brand-green); display: inline-block; }
  .letter { position: absolute; left: 44px; top: 150px; width: 420px; color: var(--ink-soft); font-size: 10px; line-height: 14px; }
  .letter__salutation { font-size: 12px; font-weight: 700; color: var(--ink); margin-bottom: 12px; }
  .letter p { margin-bottom: 13px; }
  .signature { width: 110px; height: 38px; margin-top: 6px; background: linear-gradient(90deg, #e6e6e6, #f4f4f4); border-radius: 4px; }
  .leaf-decoration {
    position: absolute; right: 30px; bottom: 150px; width: 190px; height: 180px;
    background: radial-gradient(ellipse at 55% 55%, var(--leaf-tint) 0%, var(--leaf-soft) 45%, rgba(255,255,255,0) 70%);
  }
  .footer-wave { position: absolute; left: 0; bottom: 0; width: 524px; height: 240px; }
  .footer-address { font-family: "Arimo", Arial, sans-serif; font-size: 11px; fill: #ffffff; }
</style>
</head>
<body>
  <main class="letterhead">
    <header class="brand">
      <span class="brand__dot"></span>
      <span class="brand__name">Bright Harbor Dental</span>
    </header>

    <ul class="contact">
      <li>720-555-0148 <span class="contact__icon"></span></li>
      <li>info@brightharbordental.com <span class="contact__icon"></span></li>
      <li>www.brightharbordental.com <span class="contact__icon"></span></li>
    </ul>

    <div class="leaf-decoration" role="img" aria-label="Faint green leaf decoration"></div>

    <section class="letter">
      <p class="letter__salutation">Dear Mr. Carter,</p>
      <p>Lorem ipsum is simply dummy text of the printing and typesetting industry. Lorem ipsum has been the industry's standard dummy text ever since the 1500s, when an unknown printer took a galley of type and scrambled it to make a type specimen book. It has survived not only five centuries, but also the leap into electronic typesetting, remaining essentially unchanged.</p>
      <p>The standard chunk of sample text used since the 1500s is reproduced below for those interested. Sections 1.10.32 and 1.10.33 from a classic treatise on ethics are also reproduced in their exact original form, accompanied by English versions from the 1914 translation.</p>
      <p>Lorem ipsum is simply dummy text of the printing and typesetting industry. Lorem ipsum has been the industry's standard dummy text ever since the 1500s, when an unknown printer took a galley of type and scrambled it to make a type specimen book. It has survived not only five centuries, but also the leap into electronic typesetting, remaining essentially unchanged. It was popularised in the</p>
      <div class="signature" role="img" aria-label="Handwritten signature"></div>
    </section>

    <svg class="footer-wave" viewBox="0 0 524 240">
      <path d="M0 210 C 150 170, 330 110, 524 0 L 524 8 C 340 118, 160 180, 0 222 Z" fill="var(--leaf-tint)"/>
      <path d="M0 198 C 170 165, 360 110, 524 60 L 524 240 L 0 240 Z" fill="var(--brand-green)"/>
      <text class="footer-address" x="40" y="224">2280 Lakeview Ave, Suite 210 Arvada, CO 80002</text>
    </svg>
  </main>
</body>
</html>
```